Menu Design lanterna

I need to create a take out menu for my restaurant something nice with some pictures. clean and simple with the colors of my reatsurant. which are orange and black. mostly black.

its fairly simple it has to be 4 pages front cover, inside front menu then 2nd page front and back with menu then 3rd page back front menu, back 3rd sushi menu with specials. final page 4th page, back map with adress and opening hours. and back cover final.

simple elegant and class. black and orange i will send logo and menu as well and pictures.

i am a high end bistro that serves gourmet pizza and pasta. we also have a sushi bar.
the menu will be 6 inches width by 9 inches

the menu that i sent is a pdf file. had an error with word please change font and make a new word dosument.

thank you

Industry/Entity Type

Restaurant

Requirements
Must have
• the colors which are black and orange. mostly black.

```html
<!DOCTYPE html>
<html lang="fr">
<head>
<meta charset="utf-8">
<title>Lanterna Bistro-Resto – Take Out Menu</title>
<link href="https://fonts.googleapis.com/css2?family=Roboto+Condensed:wght@400;700&family=Cormorant+Garamond:wght@500&display=swap" rel="stylesheet">
<style>
:root{
  --page:#ffffff;
  --frame:#e9ae63;
  --frame-edge:#c98a3f;
  --ink:#050505;
  --white:#f4f4f4;
  --orange:#f0a02a;
  --gold:#d9a441;
  --grey-dark:#3a3a3a;
  --grey-mid:#7d7d7d;
  --grey-light:#bdbdbd;
}
*{box-sizing:border-box;margin:0;padding:0}
html,body{width:1200px;height:849px;overflow:hidden;background:var(--page)}
body{position:relative;font-family:"Roboto Condensed",Arial,sans-serif;font-size:6px;line-height:1.28;color:var(--white)}
.panel{position:absolute;width:290px;height:408px;background:var(--frame);border:1px solid var(--frame-edge);padding:4px}
.sheet{position:relative;width:100%;height:100%;background:var(--ink);overflow:hidden}
.row-1{top:10px}.row-2{top:431px}
.col-1{left:10px}.col-2{left:307px}.col-3{left:605px}.col-4{left:903px}
.photo-strip{position:absolute;top:0;bottom:0;right:0;width:64px;background:linear-gradient(180deg,var(--grey-mid),var(--grey-dark) 18%,var(--grey-light) 35%,var(--grey-dark) 52%,var(--grey-mid) 70%,var(--grey-dark) 86%,var(--grey-light))}
.menu{position:absolute;left:12px;top:8px;width:198px}
.menu.compact{font-size:5.6px;line-height:1.25}
.section-title{text-align:center;font-weight:700;font-size:1.18em;margin:6px 0 5px;letter-spacing:.2px}
.section-title:first-child{margin-top:2px}
.item{display:flex;justify-content:space-between;gap:6px;margin-bottom:6px}
.item>:first-child{flex:1;min-width:0}
.item.tight{margin-bottom:0}
.name{text-transform:uppercase;display:block}
.desc{color:var(--orange);text-transform:uppercase;display:block}
.price{white-space:nowrap;flex-shrink:0;text-align:right}
.note{text-transform:uppercase;margin-bottom:6px}
.note.center{text-align:center}
.orange{color:var(--orange)}
.drinks{display:flex;gap:8px;margin-top:8px}
.drinks>div{flex:1;min-width:0}
.drinks .item{margin-bottom:0;gap:3px}
.drinks .section-title{text-align:left}
/* cover */
.cover-photos{position:absolute;top:0;bottom:0;left:0;width:64px;background:linear-gradient(180deg,var(--grey-light),var(--grey-dark) 20%,var(--grey-mid) 45%,var(--grey-dark) 70%,var(--grey-light))}
.cover-field{position:absolute;top:0;bottom:0;left:64px;right:0;background:linear-gradient(180deg,#2a2a2a,#444 50%,#2a2a2a)}
.brand{position:absolute;left:100px;top:22px;width:140px;height:70px;background:var(--ink);border:2px solid var(--gold);display:flex;flex-direction:column;align-items:center;justify-content:center;gap:4px}
.brand-name{display:flex;align-items:center;gap:5px;color:var(--gold);font-weight:700;font-size:20px;line-height:1}
.brand-mark{width:9px;height:9px;background:var(--gold)}
.brand-sub{color:var(--gold);font-size:7px;font-weight:700;letter-spacing:.5px}
.take-out{position:absolute;left:148px;top:362px;font-family:"Cormorant Garamond",Georgia,serif;font-size:17px;color:var(--gold)}
/* back cover */
.back-band{position:absolute;left:0;right:64px;bottom:22px;height:28px;background:linear-gradient(90deg,#2a2a2a,#555 50%,#2a2a2a)}
.back-brand{position:absolute;left:78px;bottom:26px;width:90px;height:24px;background:var(--ink);border:1px solid var(--gold);display:flex;align-items:center;justify-content:center;gap:4px;color:var(--gold);font-weight:700;font-size:10px}
.back-brand .brand-mark{width:6px;height:6px}
</style>
</head>
<body>

<!-- Front cover -->
<section class="panel row-1 col-1">
  <div class="sheet">
    <div class="cover-photos" role="img" aria-label="Black and white photos of the restaurant interior and terrace"></div>
    <div class="cover-field" role="img" aria-label="Grey and black checkered backdrop"></div>
    <div class="brand">
      <div class="brand-name"><span class="brand-mark"></span>Lanterna</div>
      <div class="brand-sub">PÂTISSERIE · SUSHI · BISTRO-RESTO</div>
    </div>
    <div class="take-out">Take Out</div>
  </div>
</section>

<!-- Pizza -->
<section class="panel row-1 col-2">
  <div class="sheet">
    <div class="photo-strip" role="img" aria-label="Strip of black and white food and dining room photos"></div>
    <div class="menu">
      <h2 class="section-title">PIZZA</h2>
      <div class="item"><div><span class="name">Margarita</span><span class="desc">Sauce tomate, mozzarella &amp; basilic</span></div><span class="price">$15.50</span></div>
      <div class="item"><div><span class="name">Champignon</span><span class="desc">Champignon, sauce tomate, mozzarella</span></div><span class="price">$17.50</span></div>
      <div class="item"><div><span class="name">Trilogie d'olive / Olive trilogy</span><span class="desc">Olives, sauce tomate piquante &amp;mozzarella<br>Olives, spicy tomato sauce &amp;mozzarella</span></div><span class="price">$17.50</span></div>
      <div class="item"><div><span class="name">Vegetarienne / Vegetarien</span><span class="desc">Legumes grillés sauce tomate &amp;mozzarella<br>Grilled veggies tomato sauce, mozzarella</span></div><span class="price">$18.50</span></div>
      <div class="item"><div><span class="name">Pizza Lanterna / Lanterna pizza</span><span class="desc">Tomates séchées, aubergine, olives, sauce, tomate&amp; mozzarella<br>Sun dried tomatoes, eggplant, olives, tomato sauce &amp; mozzarella</span></div><span class="price">$18.50</span></div>
      <div class="item"><div><span class="name">Grecque/Greek</span><span class="desc">Feta, olives, oignons rouges, mozzarella, sauce tomate<br>Feta, olives, red onions, mozzarella tomato sauce</span></div><span class="price">$19.00</span></div>
      <div class="item"><div><span class="name">Thon/Tuna</span><span class="desc">Thon, olives, sauce tomate &amp; mozzarella<br>Tuna, olives, tomato sauce &amp; mozzarella</span></div><span class="price">$18.50</span></div>
      <div class="item"><div><span class="name">Nicoise</span><span class="desc">Anchois, olives, sauce tomate &amp; mozzarella<br>Anchovies, olives mozzarella &amp; tomato sauce</span></div><span class="price">$19.00</span></div>
      <div class="item"><div><span class="name">Fruit de mar / Seafood</span><span class="desc">Crevettes, poireaux, sauce tomate &amp; mozzarella<br>Shrimp, leeks, tomato sauce &amp; mozzarella</span></div><span class="price">$19.00</span></div>
      <div class="item"><div><span class="name">Calzon</span><span class="desc">Poivron rouge, vert &amp; jaune, champignons, oignons sauce tomate &amp; mozzarella<br>Red, yellow &amp; green peppers, mushrooms, onions tomato sauce &amp; mozzarella</span></div><span class="price">$18.50</span></div>
      <div class="item tight"><span class="name">Toutes nos pizzas sont disponibles sans fromage<br>All our pizzas are available without cheese<br>Ajoutez deux oeufs / add two eggs</span><span class="price"><br><br>$1.95</span></div>
      <div class="item"><span class="name">Pate blé entier</span><span class="price">$1.25</span></div>
    </div>
  </div>
</section>

<!-- Appetizers & salads -->
<section class="panel row-1 col-3">
  <div class="sheet">
    <div class="photo-strip" role="img" aria-label="Strip of black and white food and dining room photos"></div>
    <div class="menu">
      <h2 class="section-title">ENTREES / APPETIZERS</h2>
      <div class="item"><div><span class="name">Bruschetta (6)</span><span class="desc">Tomatoes, basilic,oignons, huile d'olive<br>Tomatoes, basil, onions, olive oil &amp; garlic</span></div><span class="price">$8.50</span></div>
      <div class="item"><div><span class="name">Bruschetta au tartare de saumon (4)</span><span class="desc">Tartare de saumon, tomates, basilic, oignons, huile d'olive &amp; ail<br>Salmon tartar, tomatoes, basil, onions, olive oil &amp; garlic</span></div><span class="price">$10.25</span></div>
      <div class="item"><div><span class="name">Pain gratine / Cheese bread</span><span class="desc">Rondelle d'oignon / Onion ring<br>Soupe du jour / Soup of the day<br>Soupe a l'oignon gratinee / Onion soup<br>Crevettes a l'ail / Garlic shrimp (6) pieces</span></div><span class="price">$7.50<br>$4.50<br>$3.95<br>$6.95<br>$8.95</span></div>
      <h2 class="section-title">SALADES REPAS</h2>
      <div class="item"><div><span class="name">Salade Ceasar / Ceasar salad</span><span class="desc">Laitues, croutons, parmesan &amp; vinaigrette Ceasar maison<br>Lettuce, croutons, parmesan &amp; house Ceasar dressing made with anchovies &amp; capers</span></div><span class="price">$12.95</span></div>
      <div class="item"><div><span class="name">Salade Nicoise / Nicoise salad</span><span class="desc">Haricots, pomme de terre, thon, tomates, concombre, oeufs &amp; vinaigrette maison<br>Green beans, potatoes, tuna, tomatoes, cucumbers, eggs house vinaigrette</span></div><span class="price">$15.95</span></div>
      <div class="item"><div><span class="name">Salade fromage de chevre / Goat cheese salad</span><span class="desc">Laitues, piments, fromage de chevres, tomate, concombre<br>Lettuce, peppers, goat cheese, tomato, cucumbers</span></div><span class="price">$15.95</span></div>
      <div class="item"><div><span class="name">Salade fruit de mer / Seafood salad</span><span class="desc">Laitue, goberge, piments, mayonnaise &amp; morceaux d'orange<br>Lettuce, peppers, peppers crab sticks &amp; orange pieces</span></div><span class="price">$15.95</span></div>
      <div class="item"><div><span class="name">Salade grecque / Greek salad</span><span class="desc">Tomates, concombres, oignon rouge, olives kalamata, fromage feta<br>Tomatoes, cucumbers, red onions, red peppers, olives, feta</span></div><span class="price">$15.95</span></div>
      <div class="item"><span class="name">Salade de saumon fume capres &amp; oignons</span><span class="price">$12.95</span></div>
    </div>
  </div>
</section>

<!-- Breakfast & drinks -->
<section class="panel row-1 col-4">
  <div class="sheet">
    <div class="photo-strip" role="img" aria-label="Strip of black and white food and dining room photos"></div>
    <div class="menu">
      <h2 class="section-title">PETIT DEJEUNER / BREAKFAST</h2>
      <p class="note center orange">Servi jusqu'à 3hrs / served until 3pm</p>
      <p class="note center">Tous nos oeufs servis avec pommes de terre, fruits frais, deux tranches de pains, fromage a la creme cafe ou the avec choix de beurre ou confiture<br>All our eggs are served with potatoes, fruits two slices of toast, cream cheese, coffee or tea with choice of jam or butter.</p>
      <div class="item tight"><span class="name">Deux oeufs / Two eggs</span><span class="price">$9.50</span></div>
      <div class="item tight"><span class="name">Oeufs brouilles / Scrambled eggs (3)</span><span class="price"></span></div>
      <div class="item tight"><span class="name">Oeufs brouilles nature / Plain scrambled eggs</span><span class="price">$10.00</span></div>
      <div class="item tight"><span class="name">Oeufs brouilles &amp; asperges</span><span class="price">$10.50</span></div>
      <div class="item tight"><span class="name">Oeufs brouilles au saumon fume</span><span class="price">$12.95</span></div>
      <div class="item"><span class="name">Oeufs brouilles aux champignons</span><span class="price">$10.50</span></div>
      <div class="item tight"><span class="name">Omelette (3)</span><span class="price"></span></div>
      <div class="item tight"><span class="desc">Omelette nature / Plain omelet</span><span class="price">$10.00</span></div>
      <div class="item tight"><span class="desc">Omelette espagnole / Spanish omelet</span><span class="price">$10.50</span></div>
      <div class="item tight"><span class="desc">Omelette aux olives / Olive omelet</span><span class="price">$10.50</span></div>
      <div class="item tight"><span class="desc">Omelette aux fines herbes / Fine herb omelet</span><span class="price">$10.50</span></div>
      <div class="item tight"><span class="desc">Omelette au fromage / Cheese omelet</span><span class="price">$10.50</span></div>
      <div class="item tight"><span class="desc">Omelette aux champignons / Mushroom omelet</span><span class="price">$10.50</span></div>
      <div class="item"><span class="desc">Omelette au saumon fume / Smoked salmon omelet</span><span class="price">$12.95</span></div>
      <div class="item"><span class="name">Salade de fruit frais</span><span class="price">$4.50</span></div>
      <div class="drinks">
        <div>
          <h3 class="section-title">BOISSON CHAUDES:</h3>
          <div class="item"><span class="desc">Cafe filtre</span><span class="price">$2.00</span></div>
          <div class="item"><span class="desc">Expresso</span><span class="price">$2.50</span></div>
          <div class="item"><span class="desc">Expresso allonge</span><span class="price">$2.75</span></div>
          <div class="item"><span class="desc">Double expresso</span><span class="price">$3.00</span></div>
          <div class="item"><span class="desc">Macchiato</span><span class="price">$2.75</span></div>
          <div class="item"><span class="desc">Macchiato double</span><span class="price">$3.25</span></div>
          <div class="item"><span class="desc">Cappuccino</span><span class="price">$3.25</span></div>
          <div class="item"><span class="desc">Cappuccino bol</span><span class="price">$3.75</span></div>
          <div class="item"><span class="desc">Cafe mocha</span><span class="price">$3.75</span></div>
          <div class="item"><span class="desc">Chocolat chaud</span><span class="price">$3.75</span></div>
          <div class="item"><span class="desc">Cafe latt</span><span class="price">$3.25</span></div>
        </div>
        <div>
          <h3 class="section-title">BOISSONS FROIDES:</h3>
          <div class="item"><span class="desc">Non-fat iced cap</span><span class="price">$4.95</span></div>
          <div class="item"><span class="desc">Iced cappuccino</span><span class="price">$4.95</span></div>
          <div class="item"><span class="desc">Iced mocha</span><span class="price">$4.95</span></div>
          <div class="item"><span class="desc">Chocolat froid</span><span class="price">$3.25</span></div>
          <div class="item"><span class="desc">Ice coffee</span><span class="price">$3.95</span></div>
          <div class="item"><span class="desc">Smoothies aux fruits</span><span class="price">$4.25</span></div>
          <div class="item"><span class="desc">Selection du jour</span><span class="price"></span></div>
          <div class="item"><span class="desc">&nbsp;</span><span class="price"></span></div>
          <div class="item"><span class="desc">Jus d'orange</span><span class="price">$3.95</span></div>
          <div class="item"><span class="desc">Jus de pomme</span><span class="price"></span></div>
        </div>
      </div>
    </div>
  </div>
</section>

<!-- Fish, sides, pasta -->
<section class="panel row-2 col-1">
  <div class="sheet">
    <div class="photo-strip" role="img" aria-label="Strip of black and white food and dining room photos"></div>
    <div class="menu compact">
      <h2 class="section-title">POISSON /FISH</h2>
      <p class="note">Servi avec 2 choix de salade verte, legumes du jour, riz ou frites<br>Served with a choice of green salade, vegetables, rice or fries</p>
      <div class="item tight"><span class="name">Fish n chips</span><span class="price">$19.50</span></div>
      <div class="item tight"><span class="desc">Saumon grille / Grilled salmon</span><span class="price">$21.95</span></div>
      <div class="item tight"><span class="name">Tilapia au four</span><span class="price">$19.50</span></div>
      <div class="item tight"><span class="desc">Oven roasted tilapia</span><span class="price"></span></div>
      <div class="item tight"><span class="name">Steak de thon style tataki / Tataki style tuna steak</span><span class="price">$25.95</span></div>
      <div class="item"><span class="desc">Crevettes sautees a l'ail (10)</span><span class="price">$21.95</span></div>
      <h2 class="section-title">A COTES / SIDES</h2>
      <div class="item tight"><span class="name">Frites / French fries</span><span class="price">$3.50</span></div>
      <div class="item tight"><span class="desc">Frites epicees / Spicy french fries</span><span class="price">$4.50</span></div>
      <div class="item tight"><span class="name">Sweet potatoes fries / Frite pomme de terre douce</span><span class="price">$4.95</span></div>
      <div class="item tight"><span class="desc">Riz / Rice</span><span class="price">$3.00</span></div>
      <div class="item tight"><span class="name">Legumes grilles de saison / Seasonal grilled vegetables</span><span class="price">$5.95</span></div>
      <div class="item tight"><span class="desc">Patates / Potatoes</span><span class="price">$3.50</span></div>
      <div class="item tight"><span class="name">Salade verte /Green salad</span><span class="price">$3.25</span></div>
      <div class="item tight"><span class="desc">Thon / Tuna</span><span class="price">$3.00</span></div>
      <div class="item"><span class="name">Oeuf dur / Boiled egg</span><span class="price">$3.00</span></div>
      <h2 class="section-title">PATES / PASTA</h2>
      <p class="note center">Sauces: tomate -arabiata - alfredo -<br>pesto &amp; ail -bella rosa - marsala champignon</p>
      <div class="item tight"><span class="desc">Spaghetti</span><span class="price">$14.95</span></div>
      <div class="item tight"><span class="name">Penne</span><span class="price">$14.95</span></div>
      <div class="item tight"><span class="desc">Fettuccini</span><span class="price">$14.95</span></div>
      <div class="item tight"><span class="name">Ravioli aux champignons sauvages</span><span class="price">$17.50</span></div>
      <div class="item tight"><span class="desc">Wild mushroom ravioli</span><span class="price"></span></div>
      <div class="item tight"><span class="name">Ravioli a la ricotta épinards</span><span class="price">$17.50</span></div>
      <div class="item tight"><span class="desc">Ravioli with ricotta &amp; spinach</span><span class="price"></span></div>
      <div class="item tight"><span class="name">Ravioli a la pomme de terre douce</span><span class="price">$17.50</span></div>
      <div class="item tight"><span class="desc">Sweet potatoes ravioli</span><span class="price"></span></div>
      <div class="item tight"><span class="name">Lasagne vegetarienne</span><span class="price">$14.95</span></div>
      <div class="item tight"><span class="desc">Veggie lasagna</span><span class="price"></span></div>
      <div class="item tight"><span class="name">Sur demande</span><span class="price"></span></div>
    </div>
  </div>
</section>

<!-- Sushi starters & specialities -->
<section class="panel row-2 col-2">
  <div class="sheet">
    <div class="photo-strip" role="img" aria-label="Strip of black and white sushi and dining room photos"></div>
    <div class="menu">
      <h2 class="section-title">ENTRÉES / STARTER</h2>
      <div class="item" style="margin-bottom:10px"><span class="desc">Edamame</span><span class="price">$5.95</span></div>
      <div class="item" style="margin-bottom:10px"><span class="desc">Crevette tempura shrimp tempura</span><span class="price">$8.95</span></div>
      <div class="item" style="margin-bottom:10px"><span class="desc">Tartare de saumon salmon tartar</span><span class="price">$10.95</span></div>
      <div class="item" style="margin-bottom:10px"><span class="desc">Tartare de thon tuna tartar</span><span class="price">$13.95</span></div>
      <div class="item" style="margin-bottom:10px"><div><span class="desc">Tartare du chef chef tartar</span><span class="name">Thon, saumon avocet &amp; tobiko / tuna,salmon, advocado &amp; tobiko</span></div><span class="price">$14.95</span></div>
      <div class="item"><span class="desc">Salade de sashimi sashimi salad</span><span class="price">$16.95</span></div>
      <h2 class="section-title">SPECIALITIES' / SPECIALITIES</h2>
      <div class="item"><div><span class="name">Thon tempura (8 max)</span><span class="desc">Thon e'pice, avocet, temura, feuille de miso, riz a l'exterieur spicy tuna, avocado, tempura, miso paper, rice outside</span></div><span class="price">$9.95</span></div>
      <div class="item"><div><span class="name">Sweetie (8 max)</span><span class="desc">Pomme de terre douce, avocat, mayonnaise epice'e, feuille soya sweet potatos, avocado,spicymayo, soya paper</span></div><span class="price">$9.95</span></div>
      <div class="item"><div><span class="name">Rainbow (8 max)</span><span class="desc">Thon, saumon, avocet en arc-en-cielgoberge, concombre, feuille de nori, riz a l'exterieur tuna, salmon, avocado rainbow style, crabstick, cucumber, nori paper, rice outside</span></div><span class="price">$13.95</span></div>
      <div class="item"><div><span class="name">Incognito (6 max)</span><span class="desc">Thon e'pice', goberge, tempura,avocet, feuille de soya spicy tuna, shrimp, tempura, avocado, soya paper spicy tuna, shrimp, tempura, avocado, soya paper</span></div><span class="price">$12.95</span></div>
    </div>
  </div>
</section>

<!-- Sushi specialities, classic, hot -->
<section class="panel row-2 col-3">
  <div class="sheet">
    <div class="photo-strip" role="img" aria-label="Strip of black and white sushi and dining room photos"></div>
    <div class="menu">
      <h2 class="section-title">SPE'CIALITES/ SPECIALITIES</h2>
      <div class="item"><div><span class="name">Tunisien (8max)</span><span class="desc">Thon blanc, harissa, variante, ceuf, feuille de nori, riz a l'exte'rieur</span><span class="name">White tuna, harissa, vegetable mix, nori paper, rice outside</span></div><span class="price">$9.95</span></div>
      <div class="item"><div><span class="name">Ebi tempura(8max)</span><span class="desc">Crevette tempura, avocado, mayo sauce terrvaki</span><span class="name">Shrimp tempura, avocado, mayo terryaki sauce</span></div><span class="price">$9.95</span></div>
      <h2 class="section-title">CLASSIQUE/ CLASSIC</h2>
      <div class="item"><div><span class="name">Saumon e'pice' (8 max)</span><span class="desc">Saumon e'pice', avocado, mayo, tempura</span><span class="name">Spicy salmon, avocado, mayo, tempura</span></div><span class="price">$9.95</span></div>
      <div class="item"><div><span class="name">Kamikase(8max)</span><span class="desc">Thon e'pice', avocet, concombre,tempura, mayo</span><span class="name">Spicy tuna, avocado, cucumber, tempura, mayo</span></div><span class="price">$9.95</span></div>
      <div class="item"><div><span class="name">California(8max)</span><span class="desc">Goberge, avocet, concomber, mayo</span><span class="name">Crabstick, avocado, cucumber, mayo</span></div><span class="price">$8.95</span></div>
      <h2 class="section-title">SUSHI CHAUD/HOT SUSHI</h2>
      <div class="item"><div><span class="name">Ceil du tigre(8max)</span><span class="desc">Salmon, carotte &amp; e'chalotte</span><span class="name">Salmon, carott &amp; green onion</span></div><span class="price">$11.95</span></div>
      <div class="item"><div><span class="name">Kani frit (6max)</span><span class="desc">Goberge, povron, oignon, patate douce, avocet, mayonnaise epice'e, sauce terrvaki</span><span class="name">Crabstick, green pepper, sweet potatoe, avocado, spicy mayo, terryaki sauce</span></div><span class="price">$13.95</span></div>
      <div class="item"><div><span class="name">Deep fried california (6max)</span><span class="desc">Goberge, avocet, concomber, mayo</span><span class="name">Crabstick, avocardo, cucumber, mayo</span></div><span class="price">$10.95</span></div>
    </div>
  </div>
</section>

<!-- Back cover -->
<section class="panel row-2 col-4">
  <div class="sheet">
    <div class="photo-strip" role="img" aria-label="Strip of black and white food and dining room photos"></div>
    <div class="back-band" role="img" aria-label="Grey and black checkered band"></div>
    <div class="back-brand"><span class="brand-mark"></span>Lanterna</div>
  </div>
</section>

</body>
</html>
```